BRIGHTHOLD PROPERTY MANAGEMENT INC. WEBSITE

Please make the website more family-friendly.

I want a website to help me build my property management business by adding listing properties and creating an online application. Im open to any other ideas.
I want a WordPress designer to code it.

Here is my current website. www.brighthold.biz

IDEA: I like the website design https://www.pelicanclimateservices.com/

Thank you

Tom

Number of Pages Required

5+ page

```html
<!DOCTYPE html>
<html lang="en">
<head>
<meta charset="UTF-8">
<title>Brighthold – Landing Page Mobile View</title>
<link href="https://fonts.googleapis.com/css2?family=Poppins:wght@400;500;600;700&family=Inter:wght@400;500&display=swap" rel="stylesheet">
<style>
:root{
  --bg:#f0f0f1;
  --red:#a4232a;
  --red-soft:#f4dcdd;
  --ink:#1f2233;
  --text:#4a4a52;
  --muted:#9a9aa3;
  --dark:#333335;
  --white:#ffffff;
  --line:#e6e6ea;
  --yellow:#f6e04a;
}
*{box-sizing:border-box;margin:0;padding:0}
html,body{width:1200px;height:1200px;overflow:hidden}
body{background:var(--bg);font-family:"Poppins",sans-serif;color:var(--ink);position:relative}

.intro{position:absolute;left:40px;top:80px;width:240px}
.intro-brand{display:flex;align-items:center;gap:10px}
.intro-brand .mark{width:18px;height:18px;border-radius:50%;background:var(--red)}
.intro-brand .name{font-family:"Poppins",sans-serif;font-weight:600;color:var(--red);font-size:22px}
.intro-title{font-family:"Inter",sans-serif;font-weight:500;font-size:27px;line-height:1.25;color:var(--ink);margin-top:34px}

.screen{position:absolute;width:260px;height:540px;background:var(--white);border-radius:18px;overflow:hidden;box-shadow:0 10px 30px rgba(0,0,0,.08)}
.s1{left:320px;top:40px}.s2{left:610px;top:40px}.s3{left:900px;top:40px}
.s4{left:320px;top:620px}.s5{left:610px;top:620px}.s6{left:900px;top:620px}
.pad{padding:18px 18px}

.topbar{display:flex;justify-content:space-between;align-items:center;padding:10px 14px}
.topbar .brand{font-family:"Poppins",sans-serif;font-weight:600;color:var(--red);font-size:11px}
.burger{width:16px;height:10px;border-top:2px solid var(--ink);border-bottom:2px solid var(--ink);position:relative}
.burger::after{content:"";position:absolute;left:0;right:0;top:2px;border-top:2px solid var(--ink)}
.hero{height:210px;background:linear-gradient(180deg,#6b4f6e 0%,#4a3b44 45%,#3a3528 100%);position:relative;padding:24px 18px 0;text-align:center;color:var(--white)}
.hero h1{font-size:19px;font-weight:700;line-height:1.25}
.hero p{font-size:13px;margin-top:6px;line-height:1.3}
.search{position:absolute;left:14px;right:14px;bottom:18px;height:34px;background:var(--white);border-radius:17px;display:flex;align-items:center;padding-left:12px;font-size:8px;color:var(--muted);overflow:hidden;white-space:nowrap}
.search .go{margin-left:auto;flex:0 0 34px;width:34px;height:34px;background:var(--red);display:flex;align-items:center;justify-content:center}

.eyebrow{color:var(--red);font-size:11px;font-weight:500}
.h2{font-size:17px;font-weight:700;line-height:1.25;margin-top:4px;color:var(--ink)}
.body{font-size:8.6px;line-height:1.55;color:var(--text);margin-top:10px}

.photo{background:linear-gradient(135deg,#e7e2dc,#c8b59c 55%,#a4232a 100%)}
.why-photo{height:130px}
.center{text-align:center}
.lorem{font-size:8px;color:var(--muted);line-height:1.5;margin-top:8px}
.orbit{position:relative;height:230px;margin-top:6px}
.ring{position:absolute;left:50%;top:50%;width:130px;height:130px;margin:-65px 0 0 -65px;border-radius:50%;border:6px solid var(--red-soft)}
.core{position:absolute;left:50%;top:50%;width:96px;height:96px;margin:-48px 0 0 -48px;border-radius:50%;background:radial-gradient(circle,#d9b441 0%,#6fbf3c 55%,#4f9e2d 100%)}
.pill{position:absolute;font-size:6.5px;color:var(--red);border:1px solid var(--red);border-radius:12px;padding:4px 8px;background:var(--white);white-space:nowrap;display:flex;align-items:center;gap:4px}
.pill i{width:6px;height:6px;border-radius:2px;background:var(--red);display:block}

.field-label{font-size:9px;font-weight:500;margin-top:12px}
.field{height:32px;border:1px solid var(--line);border-radius:6px;margin-top:5px;font-size:8.5px;color:var(--muted);padding:9px 10px}
.field.tall{height:80px}
.btn-red{margin-top:16px;height:36px;border-radius:6px;background:var(--red);color:var(--white);font-size:10px;display:flex;align-items:center;justify-content:center}

.listing-photo{height:280px;background:linear-gradient(180deg,#9cc3e0 0%,#e9e4dc 45%,#8c7f6e 68%,#6aa23e 100%);position:relative}
.badge{position:absolute;left:14px;bottom:12px;background:var(--yellow);font-size:7.5px;font-weight:500;padding:3px 8px;border-radius:4px}
.price{color:var(--red);font-weight:700;font-size:16px}
.type{font-size:14px;font-weight:600;margin-top:2px}
.addr{font-size:8.5px;color:var(--muted);margin-top:4px}
.heart{position:absolute;right:18px;top:298px;width:28px;height:28px;border-radius:50%;border:1px solid var(--line);display:flex;align-items:center;justify-content:center}
.facts{display:flex;gap:12px;margin-top:10px;font-size:8px;color:var(--text)}
.facts span{display:flex;align-items:center;gap:4px}
.facts i{width:8px;height:8px;border:1.5px solid var(--red);border-radius:2px;display:block}
.btn-outline{margin-top:12px;height:32px;border:1px solid var(--red);border-radius:6px;color:var(--red);font-size:10px;display:flex;align-items:center;justify-content:center}
.btn-ghost{margin-top:8px;height:32px;border:1px solid var(--line);border-radius:6px;color:var(--muted);font-size:10px;display:flex;align-items:center;justify-content:center}

.apply{margin-top:12px;width:120px;height:32px;border-radius:6px;background:var(--red);color:var(--white);font-size:10px;display:flex;align-items:center;justify-content:center}
.rent-photo{position:absolute;left:0;right:0;bottom:0;height:170px;background:linear-gradient(160deg,#8fb2d6 0%,#e8e2cf 40%,#6f8f4c 80%,#a4232a 100%)}

.s6{background:var(--dark);color:var(--white)}
.foot-top{padding:30px 18px 20px;text-align:center;border-bottom:1px solid #48484b}
.foot-brand{font-family:"Poppins",sans-serif;font-weight:600;font-size:18px;color:var(--white);display:flex;align-items:center;justify-content:center;gap:8px}
.foot-brand .mark{width:12px;height:12px;border-radius:50%;background:var(--red)}
.foot-get{font-size:12px;font-weight:500;margin-top:16px}
.socials{display:flex;justify-content:center;gap:10px;margin-top:10px}
.socials span{width:22px;height:22px;border-radius:50%;background:var(--white)}
.foot-list{padding:18px 22px}
.foot-list h4{font-size:12px;font-weight:600;margin-bottom:8px}
.foot-list li{list-style:none;font-size:9.5px;color:#cfcfd3;margin-bottom:7px}
.foot-list ul+h4{margin-top:14px}
</style>
</head>
<body>

<section class="intro">
  <div class="intro-brand"><span class="mark"></span><span class="name">Brighthold</span></div>
  <h1 class="intro-title">Landing Page<br>Mobile view</h1>
</section>

<article class="screen s1">
  <div class="topbar"><span class="brand">Brighthold</span><span class="burger"></span></div>
  <div class="hero" role="img" aria-label="Evening photo of a modern family home">
    <h1>Welcome to Brighthold</h1>
    <p>Expert Property Management for Stress-Free Living</p>
    <div class="search">Enter address, city, zip, neighborhood, or MLS
      <span class="go"><svg width="12" height="12" viewBox="0 0 12 12"><circle cx="5" cy="5" r="3.5" fill="none" stroke="#fff" stroke-width="1.5"/><path d="M7.6 7.6L10.5 10.5" stroke="#fff" stroke-width="1.5"/></svg></span>
    </div>
  </div>
  <div class="pad">
    <div class="eyebrow">About Us</div>
    <h2 class="h2">Sacramento, Elk Grove Property Management</h2>
    <p class="body">Our vision for Brighthold Property Management is to provide the best Property Management Services to the Sacramento and surrounding areas. I am focused on providing a more personalized service to you and your tenants. This means we are a one-stop-shop. You only deal with me, no middle guy, so no time is wasted.</p>
  </div>
</article>

<article class="screen s2">
  <div class="photo why-photo" role="img" aria-label="Hands holding a tablet beside a small house model"></div>
  <div class="pad center">
    <div class="eyebrow">Why Us</div>
    <h2 class="h2">Your Property, Our Priority</h2>
    <p class="lorem">lorem ipsum dolor sit amet, consectetur adipiscing elit. Nunc vulputate libero et velit interdum, ac aliquet odio mattis.</p>
    <div class="orbit">
      <div class="ring"></div>
      <div class="core" role="img" aria-label="Small house model with a for rent tag"></div>
      <span class="pill" style="left:60px;top:4px">Tenant Screening<i></i></span>
      <span class="pill" style="left:0;top:44px">Rent Collection<i></i></span>
      <span class="pill" style="right:0;top:60px"><i></i>Leasing</span>
      <span class="pill" style="left:2px;top:112px">Repairs<i></i></span>
      <span class="pill" style="right:0;top:130px"><i></i>Inspections</span>
      <span class="pill" style="left:40px;top:196px"><i></i>Legal Support</span>
      <span class="pill" style="right:10px;top:190px"><i></i>Reports</span>
    </div>
  </div>
</article>

<article class="screen s3">
  <div class="pad">
    <div class="eyebrow">Contact Us</div>
    <h2 class="h2">Get in Touch with Brighthold We're Here to Help</h2>
    <div class="field-label">Name</div><div class="field">Your name</div>
    <div class="field-label">Email</div><div class="field">Email</div>
    <div class="field-label">Phone</div><div class="field">phone number</div>
    <div class="field-label">Message</div><div class="field tall">write message</div>
    <div class="btn-red">Submit</div>
  </div>
</article>

<article class="screen s4">
  <div class="listing-photo" role="img" aria-label="White family house with a green front lawn">
    <span class="badge">★ Available now</span>
  </div>
  <span class="heart"><svg width="12" height="11" viewBox="0 0 12 11"><path d="M6 10L1.3 5.4A2.7 2.7 0 0 1 6 2a2.7 2.7 0 0 1 4.7 3.4z" fill="none" stroke="#a4232a" stroke-width="1.2"/></svg></span>
  <div class="pad">
    <div class="price">$700</div>
    <div class="type">Type A01</div>
    <div class="addr">1420 Maple Crest, Lakeview, FL</div>
    <div class="facts"><span><i></i>3 Rooms</span><span><i></i>3 Bathrooms</span><span><i></i>12x8m²</span></div>
    <div class="btn-outline">Book Now</div>
    <div class="btn-ghost">More details</div>
  </div>
</article>

<article class="screen s5">
  <div class="pad">
    <div class="eyebrow">About Us</div>
    <h2 class="h2">Sacramento, Elk Grove Property Management</h2>
    <p class="body">Brighthold Property Management is operated and owned by me Daniel Marsh. I have over 30 years of experience in property management combined with real estate appraising and understand the importance of "return on investment".</p>
    <div class="apply">Apply now</div>
  </div>
  <div class="rent-photo" role="img" aria-label="Suburban house with a red for rent sign on the lawn"></div>
</article>

<article class="screen s6">
  <div class="foot-top">
    <div class="foot-brand"><span class="mark"></span>Brighthold</div>
    <div class="foot-get">Get In Touch</div>
    <div class="socials"><span></span><span></span><span></span></div>
  </div>
  <div class="foot-list">
    <h4>Pages</h4>
    <ul><li>Listings</li><li>Owners</li><li>Prospect Tenants</li><li>About</li><li>Community</li><li>Mortgage Info</li></ul>
    <h4>Legal</h4>
    <ul><li>Imprint</li><li>Terms&amp; Condition</li><li>Privacy</li></ul>
  </div>
</article>

</body>
</html>
```